Fastest Work at home Solution for Small Businesses

We need a web page for a product called *BrightReed*
We develop an innovative VPN Appliance (Model-Name ->Reed Alpha) that gives small business the possibility literally setup the possibility for Companies to let their employees work from home.
With our secure appliance we create safe connection between any business and the employee *working at home*
Our Products *Reed Alpha* are rolled out in minutes.
A. Employees can connect directly
B. Work from any location
C. All this without having to change the company firewall
Use case
=======
1. Go to our page
2. Select Product
3. Order
4. Connect to any Switch in the company
5. install software on employees laptop
***** INSTANT Connection ******
Target Market(s)
Businesses
Coding
Coded - Design and coding required
Number of Pages Required
3 page
Font styles to use
Look and feel
Each slider illustrates characteristics of the customer's brand and the style your logo design should communicate.

```html
<!DOCTYPE html>
<html lang="en">
<head>
<meta charset="utf-8">
<title>BrightReed – Work from home VPN appliance</title>
<link href="https://fonts.googleapis.com/css2?family=Poppins:wght@500;600;700&family=Libre+Franklin:ital,wght@0,400;0,500;0,600;1,400&display=swap" rel="stylesheet">
<style>
:root{
  --navy:#0b1c44;
  --blue:#1a3a9c;
  --accent:#1fa3c9;
  --ink:#151515;
  --text:#555;
  --muted:#f4f4f4;
  --line:#d9d9d9;
  --footer:#121212;
  --white:#fff;
}
*{margin:0;padding:0;box-sizing:border-box}
html,body{width:1200px;height:4655px;overflow:hidden}
body{position:relative;font-family:"Libre Franklin",Arial,sans-serif;color:var(--ink);background:var(--white)}
.abs{position:absolute}
.btn{position:absolute;background:var(--navy);color:var(--white);font-weight:600;font-size:15px;display:flex;align-items:center;justify-content:center}

/* header */
.site-header{top:0;left:0;width:1200px;height:90px}
.brand{display:flex;align-items:center;gap:12px;font-family:"Poppins",sans-serif;font-weight:600;font-size:40px;color:var(--navy)}
.brand-mark{width:30px;height:30px;background:var(--blue)}
.top-contact{top:12px;right:110px;display:flex;gap:26px;font-size:15px;align-items:center}
.top-contact span{display:flex;align-items:center;gap:10px}
.ic-circle{width:30px;height:30px;border-radius:50%;background:var(--accent);display:flex;align-items:center;justify-content:center}
.main-nav{top:56px;left:492px;display:flex;font-size:15px}
.main-nav a{text-decoration:none;color:var(--ink)}
.main-nav a.active{color:var(--blue)}

/* hero */
.hero{top:90px;left:0;width:1200px;height:608px;background:linear-gradient(90deg,#e4e4e2 0%,#d8d6d0 45%,#c9b58f 75%,#a88b5c 100%)}
.hero-title{top:290px;left:108px;font-family:"Poppins",sans-serif;font-weight:700;font-size:74px;line-height:96px;color:#111;letter-spacing:-1px}
.hero-text{top:394px;left:112px;width:460px;font-size:15.5px;line-height:27px;color:#222}
.dots{top:640px;left:562px;display:flex;gap:9px}
.dots i{width:11px;height:11px;border-radius:50%;background:#fff;opacity:.7}
.dots i:first-child{opacity:1}

.kicker{color:var(--blue);font-size:19px;font-weight:500}
.sec-title{font-family:"Poppins",sans-serif;font-weight:700;font-size:33px;color:#111}
.center{left:0;width:1200px;text-align:center}

/* about */
.about-art{top:780px;left:155px;width:370px;height:385px;background:linear-gradient(180deg,#2f5bb5 0%,#4a86c4 55%,#62a9cc 100%)}
.about-copy{top:795px;left:603px;width:440px}
.about-copy h2{font-family:"Poppins",sans-serif;font-weight:700;font-size:29px;line-height:35px;margin-top:14px}
.about-copy .rule{width:120px;height:2px;background:var(--accent);margin:17px 0 26px}
.about-copy p{font-size:12.5px;line-height:29px;color:var(--text)}

/* products */
.products{top:1250px;left:0;width:1200px;height:660px;background:var(--muted)}
.card{position:absolute;top:1413px;width:311px;height:427px;background:#fff}
.card .ph{height:213px}
.card h3{font-family:"Poppins",sans-serif;font-weight:600;font-size:17px;line-height:27px;margin:20px 14px 6px}
.card p{font-size:11.5px;line-height:26px;color:var(--text);margin:0 14px}
.card a{display:block;margin:10px 14px;font-weight:600;font-size:14px;color:#111;text-decoration:none}

/* how */
.step{position:absolute;top:2074px;width:200px;text-align:center;font-size:15px;line-height:21px}
.step .ring{width:112px;height:112px;border-radius:50%;border:1.5px solid var(--line);margin:0 auto 18px;display:flex;align-items:center;justify-content:center;background:#fff}
.dash{position:absolute;top:2130px;height:0;border-top:2px dashed var(--line)}

/* video */
.video-band{top:2400px;left:0;width:1200px;height:387px;background:linear-gradient(180deg,#0b1c44,#17306a)}
.video-rest{top:2787px;left:0;width:1200px;height:753px;background:var(--muted)}
.video-box{top:2617px;left:139px;width:922px;height:413px;background:linear-gradient(135deg,#2e3f5e 0%,#5f7291 45%,#1f2a3f 100%)}
.play{top:2775px;left:555px;width:90px;height:90px;border-radius:50%;background:#fff;border:3px solid var(--navy);display:flex;align-items:center;justify-content:center}

/* testimonials */
.quote{position:absolute;top:3208px;width:468px;height:194px;background:#fff;box-shadow:0 2px 8px rgba(0,0,0,.08);padding:30px 25px;font-style:italic;font-size:13px;line-height:28px;color:#444}
.author{position:absolute;top:3424px;display:flex;gap:12px;align-items:center}
.author .av{width:36px;height:36px;border-radius:50%;background:#9aa4b3}
.author b{font-weight:500;font-size:14px;display:block}
.author small{font-size:9px;color:#555}
.arrow{position:absolute;top:3289px;width:27px;height:27px;border-radius:50%;border:1.5px solid var(--accent);display:flex;align-items:center;justify-content:center}

/* blog */
.post-img{position:absolute}
.meta{position:absolute;font-size:13px;color:var(--blue);display:flex;gap:7px;align-items:center}
.post-title{position:absolute;font-family:"Poppins",sans-serif;font-weight:500;font-size:16px;line-height:27px;color:#111}

/* footer */
.site-footer{top:4292px;left:0;width:1200px;height:363px;background:var(--footer);color:#fff}
.f-col{position:absolute;top:80px;font-size:13.5px;line-height:28px}
.f-col h4{font-family:"Poppins",sans-serif;font-weight:600;font-size:15px;margin-bottom:10px}
.f-col h4::after{content:"";display:block;width:68px;height:2px;background:#fff;margin-top:8px}
.social{display:flex;gap:10px;margin-top:22px}
.social i{width:31px;height:31px;border-radius:50%;background:#fff}
.sub{display:flex;align-items:center;width:265px;height:44px;border-radius:22px;background:#fff;color:#888;padding-left:18px;font-size:13px;justify-content:space-between;margin-top:16px}
.sub span.go{width:44px;height:44px;border-radius:50%;background:var(--navy);display:flex;align-items:center;justify-content:center}
</style>
</head>
<body>

<header class="site-header abs">
  <div class="brand abs" style="top:18px;left:110px"><span class="brand-mark"></span>BrightReed</div>
  <div class="top-contact abs">
    <span><i class="ic-circle"><svg width="14" height="14" viewBox="0 0 24 24"><path fill="#fff" d="M6.6 10.8a15 15 0 0 0 6.6 6.6l2.2-2.2c.3-.3.7-.4 1-.2 1.1.4 2.3.6 3.6.6.6 0 1 .4 1 1V20c0 .6-.4 1-1 1A17 17 0 0 1 3 4c0-.6.4-1 1-1h3.5c.6 0 1 .4 1 1 0 1.3.2 2.5.6 3.6.1.3 0 .7-.2 1z"/></svg></i>(555)-014-2290</span>
    <span><i class="ic-circle"><svg width="15" height="12" viewBox="0 0 24 18"><rect x="1" y="1" width="22" height="16" fill="none" stroke="#fff" stroke-width="2"/><path d="M1 1l11 9 11-9" fill="none" stroke="#fff" stroke-width="2"/></svg></i>info@brightreed.com</span>
  </div>
  <nav class="main-nav abs">
    <a class="active" href="#" style="margin-right:69px">Home</a>
    <a href="#" style="margin-right:73px">About us</a>
    <a href="#" style="margin-right:72px">Our Products</a>
    <a href="#" style="margin-right:67px">Blog</a>
    <a href="#">Contact Us</a>
  </nav>
</header>

<section class="hero abs" role="img" aria-label="Photo of a smiling woman with a headset working on a laptop at a home desk"></section>
<svg class="abs" style="top:384px;left:74px" width="14" height="24" viewBox="0 0 14 24"><path d="M12 2L2 12l10 10" fill="none" stroke="#fff" stroke-width="2"/></svg>
<svg class="abs" style="top:384px;left:1112px" width="14" height="24" viewBox="0 0 14 24"><path d="M2 2l10 10L2 22" fill="none" stroke="#fff" stroke-width="2"/></svg>
<h1 class="hero-title abs">BrightReed</h1>
<p class="hero-text abs">Lorem ipsum dolor sit amet, consectetur adipiscing elit, sed do eiusmod tempor incididunt ut labore et dolore magna aliqua.</p>
<a class="btn" style="top:472px;left:113px;width:140px;height:43px">Get Started</a>
<div class="dots abs"><i></i><i></i><i></i><i></i></div>

<!-- about -->
<div class="about-art abs" role="img" aria-label="Illustration of circular photo tiles of remote workers in blue tones"></div>
<div class="about-copy abs">
  <div class="kicker">About Our Company</div>
  <h2>WE DEVELOP AN INNOVATIVE VPN APPLIANCE</h2>
  <div class="rule"></div>
  <p>Lorem ipsum dolor sit amet, consectetur adipiscing elit, sed do eiusmod tempor incididunt ut labore et dolore maaliqua. Quis ipsum suspendisse ultrices gravida. Risus commodo viverra maecenas accumsan lacus vel facilisis. Lorem ipsum dolor sit amet, consectetur adipiscing elit, sed do eiusmod tempor incididunt ut labore et</p>
</div>
<a class="btn" style="top:1100px;left:603px;width:141px;height:43px">Learn More</a>

<!-- products -->
<section class="products abs"></section>
<div class="kicker abs center" style="top:1316px">Reed Alpha* are rolled out in minutes</div>
<h2 class="sec-title abs center" style="top:1348px">OUR PRODUCTS</h2>
<article class="card" style="left:111px"><div class="ph" role="img" aria-label="Photo of a woman with a headset on a video call at her laptop" style="background:linear-gradient(135deg,#c9c2b5,#7d746a)"></div>
  <h3>Employees can connect directly</h3>
  <p>Lorem ipsum dolor sit amet, consectet adipiscing elit, sed do eiusmod tempor incididunt ut labore et dolore magna aliqua.</p><a>Read More &gt;&gt;</a></article>
<article class="card" style="left:444px"><div class="ph" role="img" aria-label="Night city skyline photo with location markers" style="background:linear-gradient(180deg,#2a4a78,#b07a3c)"></div>
  <h3>Work from any location</h3>
  <p>Lorem ipsum dolor sit amet, consectet adipiscing elit, sed do eiusmod tempor incididunt ut labore et dolore magna aliqua.Lorem ipsum dolor sit amet, consectet adipiscing elit</p><a>Read More &gt;&gt;</a></article>
<article class="card" style="left:776px"><div class="ph" role="img" aria-label="Photo of hands at a laptop with glowing security lock graphics" style="background:linear-gradient(135deg,#1d2a44,#5b86b8)"></div>
  <h3 style="margin-right:8px">All this without having to change the company firewall</h3>
  <p>Lorem ipsum dolor sit amet, consectet adipiscing elit, sed do eiusmod tempor incididunt ut labore et dolore magna aliqua.</p><a>Read More &gt;&gt;</a></article>

<!-- how it works -->
<div class="kicker abs center" style="top:1955px">Use case</div>
<h2 class="sec-title abs center" style="top:1987px">HOW IT WORK</h2>
<div class="dash" style="left:251px;width:76px"></div>
<div class="dash" style="left:439px;width:80px"></div>
<div class="dash" style="left:631px;width:105px"></div>
<div class="dash" style="left:848px;width:116px"></div>
<div class="step" style="left:95px"><div class="ring"><svg width="50" height="44" viewBox="0 0 50 44" fill="none" stroke="#1a3a9c" stroke-width="2"><rect x="2" y="2" width="46" height="36"/><path d="M2 10h46"/><circle cx="25" cy="25" r="10"/><path d="M15 25h20M25 15v20"/></svg></div>Go to our page</div>
<div class="step" style="left:283px"><div class="ring"><svg width="44" height="50" viewBox="0 0 44 50" fill="none" stroke="#1a3a9c" stroke-width="2"><rect x="6" y="2" width="32" height="46"/><path d="M12 12h20M12 20h20M12 28h20M12 36h14"/></svg></div>Select Product</div>
<div class="step" style="left:475px"><div class="ring"><svg width="50" height="46" viewBox="0 0 50 46" fill="none" stroke="#1a3a9c" stroke-width="2"><rect x="2" y="2" width="46" height="32"/><path d="M18 44h14M25 34v10"/><path d="M14 12h4l4 12h12l3-9H20"/></svg></div>Order</div>
<div class="step" style="left:692px"><div class="ring"><svg width="52" height="50" viewBox="0 0 52 50" fill="none" stroke="#1a3a9c" stroke-width="2"><circle cx="26" cy="25" r="8"/><circle cx="9" cy="9" r="6"/><circle cx="43" cy="9" r="6"/><circle cx="9" cy="41" r="6"/><circle cx="43" cy="41" r="6"/><path d="M14 14l6 6M38 14l-6 6M14 36l6-6M38 36l-6-6"/></svg></div>Connect to any Switch<br>in the company</div>
<div class="step" style="left:920px"><div class="ring"><svg width="52" height="42" viewBox="0 0 52 42" fill="none" stroke="#1a3a9c" stroke-width="2"><rect x="8" y="2" width="36" height="28"/><path d="M2 38h48l-4-8H6z"/><circle cx="26" cy="16" r="6"/></svg></div>install software on<br>employees laptop</div>
<a class="btn" style="top:2274px;left:530px;width:140px;height:41px">Get Started</a>

<!-- video -->
<section class="video-band abs"></section>
<section class="video-rest abs"></section>
<h2 class="sec-title abs center" style="top:2476px;color:#fff">WATCH OUR VIDEO</h2>
<p class="abs center" style="top:2528px;color:#fff;font-size:16px;line-height:28px">Lorem ipsum dolor sit amet, consectetur adipiscing elit, sed do eiusmod<br>tempor incididunt ut labore et dolore magna aliqua.</p>
<div class="video-box abs" role="img" aria-label="Video still of hands typing on a laptop keyboard"></div>
<div class="play abs"><svg width="22" height="24" viewBox="0 0 22 24"><path d="M4 2l16 10L4 22z" fill="#0b1c44"/></svg></div>

<!-- testimonials -->
<div class="kicker abs center" style="top:3104px">Review</div>
<h2 class="sec-title abs center" style="top:3136px">OUR TESTIMONIALS</h2>
<div class="arrow" style="left:66px"><svg width="8" height="12" viewBox="0 0 8 12"><path d="M7 1L2 6l5 5" fill="none" stroke="#1fa3c9" stroke-width="1.5"/></svg></div>
<div class="arrow" style="left:1106px"><svg width="8" height="12" viewBox="0 0 8 12"><path d="M1 1l5 5-5 5" fill="none" stroke="#1fa3c9" stroke-width="1.5"/></svg></div>
<blockquote class="quote" style="left:113px">Lorem ipsum dolor sit amet, consectetur adig elit, sed do eiusmod tempor incididunt ut labore et dolore magna aliqua. Quis ipsum suspendisse ultrices gravida. Risus commodo viverra maecenas accumsan lacus vel facilisis.</blockquote>
<blockquote class="quote" style="left:619px">Lorem ipsum dolor sit amet, consectetur adig elit, sed do eiusmod tempor incididunt ut labore et dolore magna aliqua. Quis ipsum suspendisse ultrices gravida. Risus commodo viverra maecenas accumsan lacus vel facilisis.</blockquote>
<div class="author" style="left:126px"><span class="av" role="img" aria-label="Reviewer portrait"></span><div><b>Daniel Brooks</b><small>Lorem ipsum dolor sit amet,</small></div></div>
<div class="author" style="left:632px"><span class="av" role="img" aria-label="Reviewer portrait"></span><div><b>Daniel Brooks</b><small>Lorem ipsum dolor sit amet,</small></div></div>

<!-- blog -->
<div class="kicker abs center" style="top:3619px">What We Provide</div>
<h2 class="sec-title abs center" style="top:3651px">OUR LATEST BLOG</h2>
<div class="post-img" role="img" aria-label="Photo of a lightbox sign reading work from home beside a laptop and plant" style="top:3724px;left:111px;width:472px;height:293px;background:linear-gradient(135deg,#b9a88f,#6f6a62)"></div>
<div class="meta" style="top:4042px;left:111px">▦ 15 April,2021</div>
<div class="post-title" style="top:4070px;left:111px;width:470px;font-size:18px;line-height:28px">Lorem ipsum dolor simet, consectetr adipiscing elit, sed do eiusmod tempor</div>
<p class="abs" style="top:4135px;left:111px;width:470px;font-size:11.5px;line-height:26px;color:#555">Lorem ipsum dolor sit amet, consectetur adipiscineiusmod tempor incididunt ut labore et dolore magna aliqua. Quis ipsum pendisse ultrices gravida.</p>

<div class="post-img" role="img" aria-label="Overhead photo of a desk with laptops" style="top:3724px;left:601px;width:237px;height:146px;background:linear-gradient(135deg,#6b4a34,#c8beb2)"></div>
<div class="post-img" role="img" aria-label="Photo of a woman working on a laptop at home" style="top:3724px;left:852px;width:237px;height:146px;background:linear-gradient(135deg,#2f4c6e,#8fa1b2)"></div>
<div class="post-img" role="img" aria-label="Photo of a man working at a laptop in an office" style="top:3984px;left:601px;width:237px;height:146px;background:linear-gradient(135deg,#8a7a68,#d7cdbf)"></div>
<div class="post-img" role="img" aria-label="Overhead photo of a laptop surrounded by papers" style="top:3984px;left:852px;width:237px;height:146px;background:linear-gradient(135deg,#c9c6cf,#6e6a80)"></div>
<div class="meta" style="top:3886px;left:601px">▦ 15 April,2020</div>
<div class="meta" style="top:3886px;left:852px">▦ 15 April,2021</div>
<div class="meta" style="top:4146px;left:601px">▦ 15 April,2020</div>
<div class="meta" style="top:4146px;left:852px">▦ 15 April,2020</div>
<div class="post-title" style="top:3908px;left:601px;width:240px">Lorem ipsum dolorcoectetur adipiscing elit, sed do</div>
<div class="post-title" style="top:3908px;left:852px;width:240px">Lorem ipsum dolorcoectetur adipiscing elit, sed do</div>
<div class="post-title" style="top:4168px;left:601px;width:240px">Lorem ipsum dolorcoectetur adipiscing elit, sed do</div>
<div class="post-title" style="top:4168px;left:852px;width:240px">Lorem ipsum dolorcoectetur adipiscing elit, sed do</div>

<!-- footer -->
<footer class="site-footer abs">
  <div class="f-col" style="left:110px;top:70px;width:240px;font-size:11.5px;line-height:22px">
    <div class="brand" style="color:#fff;font-size:32px;gap:10px;margin-bottom:14px"><span class="brand-mark" style="width:22px;height:22px;background:#fff"></span>BrightReed</div>
    Lorem ipsum dolor sit amet, consectetur adipiscing elit, sed do eiusmod tempor incididunt ut labore et <u>Read more..</u>
    <div class="social"><i></i><i></i><i></i><i></i></div>
  </div>
  <div class="f-col" style="left:356px"><h4>QUICK LINKS</h4>Home<br>About<br>Our Products<br>Blog<br>Contact Us</div>
  <div class="f-col" style="left:544px;width:240px"><h4>CONTACT US</h4>
    <div style="display:flex;gap:12px;line-height:22px;margin-top:12px"><span>⦿</span><span>48 Harbor Lane, Fairview 20417, United States</span></div>
    <div style="display:flex;gap:12px;margin-top:10px"><span>☎</span><span>555 014 2290</span></div>
    <div style="display:flex;gap:12px;margin-top:10px"><span>✉</span><span>info@brightreed.com</span></div>
  </div>
  <div class="f-col" style="left:824px;width:270px"><h4>SUBSCRIBE TO OUR BLOG</h4>
    Sign up today to get resources on how to attract and retain more customers!
    <div class="sub">✉ Email Address<span class="go"><svg width="18" height="18" viewBox="0 0 24 24"><path d="M2 12L22 3l-6 19-4-8z" fill="#fff"/></svg></span></div>
  </div>
  <div class="abs" style="top:303px;left:110px;width:980px;height:1px;background:#444"></div>
  <div class="abs" style="top:326px;left:0;width:1200px;text-align:center;font-size:13px">Copyright © 2021.BrightReed.All Rights Reserved</div>
</footer>
</body>
</html>
```